Specialised investor in e-mobility and energy wants business card design

We need a business card design that fits our existing corporate design. <The look and feel must be 'sharp'/'clean', dynamic, communicate momentum, professionalism etc (as one would imagine from a firm in the financial sector). We like the idea of a reverse-side of the card that includes the logo, and the name and contact details on the other. We expect the deliverable to be whatever format might be required to be able to get cards printed directly by a service such as kelmo press. Our website is www.zub.capital

```html
<!DOCTYPE html>
<html lang="en">
<head>
<meta charset="utf-8">
<title>Zub Capital – Business Card</title>
<link rel="stylesheet" href="https://fonts.googleapis.com/css2?family=Arimo:wght@400;700&display=swap">
<style>
  :root {
    --stage: #161816;
    --card: #2b4a1f;
    --card-deep: #223d18;
    --edge: #6fae3c;
    --accent: #72b23e;
    --text: #ffffff;
    --text-soft: #e6eee0;
  }
  * { box-sizing: border-box; margin: 0; padding: 0; }
  html, body {
    width: 1200px; height: 963px; overflow: hidden;
    background: var(--stage);
    font-family: "Arimo", Arial, sans-serif;
  }
  .sheet {
    position: relative; width: 1200px; height: 963px;
    display: flex; flex-direction: column; align-items: center;
    justify-content: center; gap: 40px;
  }
  .card {
    position: relative; width: 720px; height: 412px;
    background: var(--card);
    border-radius: 30px;
    border-bottom: 4px solid var(--edge);
    overflow: hidden;
  }
  .brand-name {
    color: var(--text); font-weight: 400; font-size: 46px;
    letter-spacing: 1px; display: flex; align-items: center; gap: 14px;
    white-space: nowrap;
  }
  .brand-dot {
    width: 14px; height: 14px; border-radius: 50%; background: var(--accent);
  }

  /* Front */
  .card--front .brand-name { position: absolute; left: 62px; top: 170px; }
  .card--front .divider {
    position: absolute; left: 376px; top: 110px; width: 1px; height: 200px;
    background: var(--text-soft);
  }
  .details { position: absolute; left: 408px; top: 122px; color: var(--text); }
  .person {
    font-weight: 700; font-size: 20px; letter-spacing: 1px; text-transform: uppercase;
    white-space: nowrap;
  }
  .person .surname { color: var(--accent); }
  .location { font-size: 16px; margin-top: 14px; color: var(--text-soft); }
  .contacts { list-style: none; margin-top: 22px; }
  .contacts li {
    display: flex; align-items: center; gap: 12px;
    font-size: 16px; color: var(--text-soft); margin-bottom: 11px;
    white-space: nowrap;
  }
  .contacts svg { width: 18px; height: 18px; flex: none; }

  /* Back */
  .card--back .brand-name { position: absolute; left: 56px; top: 48px; z-index: 2; }
  .decor {
    position: absolute; inset: 0;
    background:
      radial-gradient(ellipse at 70% 110%, rgba(84,150,46,0.55), transparent 55%),
      linear-gradient(160deg, var(--card) 35%, var(--card-deep) 70%, #2f5a21 100%);
  }
</style>
</head>
<body>
<main class="sheet">
  <section class="card card--front" aria-label="Card front">
    <div class="brand-name"><span class="brand-dot"></span>Zub Capital</div>
    <div class="divider"></div>
    <div class="details">
      <p class="person">Peter <span class="surname">Halloway</span></p>
      <p class="location">Lugano, Switzerland</p>
      <ul class="contacts">
        <li>
          <svg viewBox="0 0 24 24" aria-hidden="true"><path fill="var(--accent)" d="M6.6 10.8a15.1 15.1 0 0 0 6.6 6.6l2.2-2.2a1 1 0 0 1 1-.25 11.4 11.4 0 0 0 3.6.57 1 1 0 0 1 1 1V20a1 1 0 0 1-1 1A17 17 0 0 1 3 4a1 1 0 0 1 1-1h3.5a1 1 0 0 1 1 1c0 1.25.2 2.45.57 3.570a1 1 0 0 1-.25 1z"/></svg>
          +41 70415 2287
        </li>
        <li>
          <svg viewBox="0 0 24 24" aria-hidden="true"><rect x="2" y="5" width="20" height="14" rx="1.5" fill="var(--accent)"/><path d="M3 6l9 7 9-7" fill="none" stroke="var(--card)" stroke-width="1.6"/></svg>
          peter@zub.capital
        </li>
        <li>
          <svg viewBox="0 0 24 24" aria-hidden="true"><circle cx="12" cy="12" r="9" fill="none" stroke="var(--accent)" stroke-width="2"/><ellipse cx="12" cy="12" rx="4" ry="9" fill="none" stroke="var(--accent)" stroke-width="1.6"/><path d="M3 12h18" stroke="var(--accent)" stroke-width="1.6"/></svg>
          www.zub.capital
        </li>
      </ul>
    </div>
  </section>

  <section class="card card--back" aria-label="Card back">
    <div class="decor" role="img" aria-label="Large faint embossed brand symbol decoration in deep greens"></div>
    <div class="brand-name"><span class="brand-dot"></span>Zub Capital</div>
  </section>
</main>
</body>
</html>
```